Online Dating Website called WinkAtWheel.com

PLEASE CAN ALL PARTICIPATING DESIGNERS PLEASE SUBMIT ALL PAGES AS DETAILED IN THE ORIGINAL BRIEF BELOW WITHIN 48 HOURS TO AVOID WINKATWHEEL EXTENDING THE CONTEST FURTHER.

We have an online dating website that is 95% fully functional and now require an exciting and creative designer to help us create the best dating experience. We are looking for your ideas on a couple of our key pages. These are our landing, profile and search page. We already have a homepage that we are happy with and winning designers will look to build upon the foundations of the homepage and extend them through their designs.

The premise of the site is the idea that if you've ever seen someone out driving and wished you could communicate because you found them attractive, how would you? Well with WinkAtWheel.com you can. Just enter their vehicle registration number (license plate) in to the website in order to get in touch, flirt and develop a relationship. It also allows users to find each other based on other criteria. It acts as both a specialist service and a normal dating website.

The pages that require developing are 1) our landing page, this is the page users see when they first login to the site, it comprises various pieces of information but it's primary function is a live feed of events generated based on the users favourited profiles and interactions with the user. 2) The profile page is the page where users can edit their own information, given the nature of this page we are looking for a creative design that gives this page some flair. 3) Finally we are looking for ideas for our search page, this page needs to provide a list of users who meet the user's search requirements and display the profile of a selected user.
Updates

Project Deadline Extended
Reason: We've asked for certain pages in our brief to be designed and this still hasn't been done. We've contacted the designers that have currently submitted designs and requested this several times. We still await for this to happen.

Target Market(s)

Male or Female age 18+

Industry/Entity Type

Dating

Requirements
Must have
• Our must have feature is a designer with an open mind. The functionality of the site must be present, all we ask is for you to be creative with the layout. Think out side of the box, change the colours, the layout, and the background as you feel. Make it look current and appealing to the user.
Nice to have
• Theme's carried through from the home page
Should not have
• Do not include Comic Sans or Times New Roman font in your designs.

```html
<!DOCTYPE html>
<html lang="en">
<head>
<meta charset="utf-8">
<title>WinkAtWheel.com – Live Feed</title>
<link rel="stylesheet" href="https://fonts.googleapis.com/css2?family=Arimo:wght@400;700&family=Open+Sans:wght@400;700&display=swap">
<style>
:root{
  --sky-top:#1a9fdc;
  --sky-mid:#2bb3ec;
  --sky-low:#34bff2;
  --panel:#efefef;
  --panel-edge:#ffffff;
  --ink:#333333;
  --ink-soft:#555555;
  --orange-top:#ffa43a;
  --orange-low:#f57f14;
  --green-top:#9ad23c;
  --green-low:#5fa514;
  --blue-btn-top:#7fd0f5;
  --blue-btn-low:#2aa4e2;
  --search-btn:#1e9ad8;
  --like:#7fcf4e;
  --time:#1c3a5a;
  --rule:#d4d4d4;
  --footer-top:#1a1a1e;
  --footer-low:#404044;
  --footer-ink:#ffffff;
  --bubble:#3d8fd0;
}
*{box-sizing:border-box;margin:0;padding:0}
html,body{width:1156px;height:1200px;overflow:hidden}
body{position:relative;font-family:"Arimo",Arial,sans-serif;color:var(--ink);
  background:linear-gradient(160deg,var(--sky-top) 0%,var(--sky-mid) 55%,var(--sky-low) 100%)}
.panel{position:absolute;background:var(--panel);border:3px solid var(--panel-edge);box-shadow:0 1px 3px rgba(0,0,0,.25);overflow:hidden}
.pill{position:absolute;left:9px;right:9px;height:30px;border:1px solid rgba(0,0,0,.15);
  font-weight:700;font-size:15px;text-align:center;line-height:28px;letter-spacing:.3px;color:#1d2a33}
.pill--green{background:linear-gradient(var(--green-top),var(--green-low))}
.pill--blue{background:linear-gradient(var(--blue-btn-top),var(--blue-btn-low))}
.photo{position:absolute;border:3px solid #fff;box-shadow:0 0 2px rgba(0,0,0,.35);
  background:linear-gradient(135deg,#6f9a45 0%,#b5623e 55%,#3d4f7a 100%)}

/* top summary */
.stats{left:9px;top:-10px;width:212px;height:63px;font-size:11px}
.stats p{position:absolute;left:15px;right:15px;display:flex;justify-content:space-between}

/* filter */
.filter{left:9px;top:70px;width:212px;height:399px}
.filter h3{position:absolute;left:15px;font-size:13px;font-weight:700;color:#333}
.filter ul{position:absolute;left:15px;list-style:none;font-size:11px;line-height:15.8px;color:var(--ink-soft)}
.rule{position:absolute;left:15px;right:9px;height:1px;background:var(--rule)}

/* favourites */
.favs{left:9px;top:486px;width:212px;height:483px}
.favs input{position:absolute;left:9px;top:48px;width:110px;height:23px;border:1px solid #bbb;background:#fff;
  font:11px "Arimo",Arial,sans-serif;padding-left:6px;color:#555}
.favs button{position:absolute;left:126px;top:48px;width:73px;height:23px;border:0;background:var(--search-btn);
  color:#fff;font:13px "Arimo",Arial,sans-serif}
.fav{position:absolute;left:9px;width:188px;height:94px}
.fav .photo{left:0;top:0;width:68px;height:56px}
.fav .who{position:absolute;left:74px;top:-2px;font-size:11px;line-height:15.8px;color:var(--ink-soft)}
.fav .who b{font-size:12px;color:#222}

/* feed */
.card{left:236px;width:655px;height:152px}
.card-head{position:absolute;left:4px;right:4px;top:3px;height:30px;
  background:linear-gradient(var(--orange-top),var(--orange-low));border:1px solid #e27410;
  color:#fff;font-weight:700;font-size:14.5px;line-height:28px;padding-left:15px}
.card .photo{left:6px;top:40px;width:75px;height:62px}
.card-text{position:absolute;left:90px;top:47px;font-size:11px;color:#333}
.card-time{position:absolute;left:9px;top:115px;font-size:11px;color:var(--time)}
.card-like{position:absolute;left:12px;top:135px;font-size:11px;color:var(--like);display:flex;align-items:center;gap:3px}

/* right column */
.matches{left:906px;top:-10px;width:212px;height:43px;font-size:12px;font-weight:700;color:#222}
.matches span{position:absolute;top:10px}
.bg-select{left:906px;top:50px;width:212px;height:306px}
.thumb{position:absolute;width:56px;height:56px;border:2px solid #fff;box-shadow:0 0 2px rgba(0,0,0,.4)}

/* footer */
.footer{position:absolute;left:0;top:1011px;width:1156px;height:189px;
  background:linear-gradient(var(--footer-top),var(--footer-low));
  font-family:"Open Sans",Arial,sans-serif;color:var(--footer-ink);font-size:11px}
.footer h4{position:absolute;top:40px;font-size:11px;font-weight:700}
.footer ul{position:absolute;top:72px;list-style:none;line-height:15px}
.copyright{position:absolute;left:41px;top:148px}
.tweet{position:absolute;left:763px;top:40px;width:295px;height:50px;background:var(--bubble);border-radius:6px;
  padding:10px 9px;font-size:10.5px}
.tweet-tail{position:absolute;left:1003px;top:89px}
.social{position:absolute;top:120px;font-size:12px;display:flex;align-items:center;gap:5px}
.social i{display:inline-block;width:7px;height:7px;background:#fff}
</style>
</head>
<body>

<section class="panel stats">
  <p style="top:14px"><span>Your favourites</span><span>12</span></p>
  <p style="top:30px"><span>Favourited by</span><span>8</span></p>
</section>

<nav class="panel filter">
  <div class="pill pill--green" style="top:8px">FEED FILTER</div>
  <h3 style="top:47px">STATUS UPDATES</h3>
  <ul style="top:67px"><li>Statuses by others</li><li>Statuses by me</li></ul>
  <div class="rule" style="top:109px"></div>
  <h3 style="top:124px">IMAGE UPLOADS</h3>
  <ul style="top:144px"><li>Uploads by others</li><li>Uploads by me</li></ul>
  <div class="rule" style="top:189px"></div>
  <h3 style="top:205px">PROFILE UPDATES</h3>
  <ul style="top:225px"><li>Updates by otheeres</li><li>Updates By Me</li><li>Image changes by others</li><li>Image changes by me</li></ul>
  <div class="rule" style="top:300px"></div>
  <h3 style="top:315px">OTHERS</h3>
  <ul style="top:335px"><li>Received Messages</li><li>Views</li><li>favouring</li></ul>
</nav>

<aside class="panel favs">
  <div class="pill pill--blue" style="top:10px">YOUR FAVOURITES</div>
  <input type="text" value="Type a name..">
  <button>Search</button>
  <div class="fav" style="top:88px"><div class="photo" role="img" aria-label="Profile photo"></div><p class="who"><b>Maisie</b><br>22 years old<br>Leeds</p></div>
  <div class="rule" style="top:162px;left:9px"></div>
  <div class="fav" style="top:182px"><div class="photo" role="img" aria-label="Profile photo"></div><p class="who"><b>Maisie</b><br>22 years old<br>Leeds</p></div>
  <div class="rule" style="top:256px;left:9px"></div>
  <div class="fav" style="top:276px"><div class="photo" role="img" aria-label="Profile photo"></div><p class="who"><b>Maisie</b><br>22 years old<br>Leeds</p></div>
  <div class="rule" style="top:350px;left:9px"></div>
  <div class="fav" style="top:370px"><div class="photo" role="img" aria-label="Profile photo"></div><p class="who"><b>Maisie</b><br>22 years old<br>Leeds</p></div>
  <div class="rule" style="top:444px;left:9px"></div>
</aside>

<main>
  <article class="panel card" style="top:-16px">
    <h2 class="card-head">Lady changed her status</h2>
    <div class="photo" role="img" aria-label="Member profile photo"></div>
    <p class="card-text">Lorem ipsum dolor sit amet, consectetur adipiscing elit. Maecenas fermentum ante id pellentesque consequat.</p>
    <p class="card-time">TuesDay 22:37</p>
    <p class="card-like"><svg width="9" height="8" viewBox="0 0 10 9"><path d="M5 9 0.8 4.6A2.4 2.4 0 0 1 5 1.6a2.4 2.4 0 0 1 4.2 3z" fill="var(--like)"/></svg>Like</p>
  </article>
  <article class="panel card" style="top:151px">
    <h2 class="card-head">Lady changed her status</h2>
    <div class="photo" role="img" aria-label="Member profile photo"></div>
    <p class="card-text">Lorem ipsum dolor sit amet, consectetur adipiscing elit. Maecenas fermentum ante id pellentesque consequat.</p>
    <p class="card-time">TuesDay 22:37</p>
    <p class="card-like"><svg width="9" height="8" viewBox="0 0 10 9"><path d="M5 9 0.8 4.6A2.4 2.4 0 0 1 5 1.6a2.4 2.4 0 0 1 4.2 3z" fill="var(--like)"/></svg>Like</p>
  </article>
  <article class="panel card" style="top:317px">
    <h2 class="card-head">Lady changed her status</h2>
    <div class="photo" role="img" aria-label="Member profile photo"></div>
    <p class="card-text">Lorem ipsum dolor sit amet, consectetur adipiscing elit. Maecenas fermentum ante id pellentesque consequat.</p>
    <p class="card-time">TuesDay 22:37</p>
    <p class="card-like"><svg width="9" height="8" viewBox="0 0 10 9"><path d="M5 9 0.8 4.6A2.4 2.4 0 0 1 5 1.6a2.4 2.4 0 0 1 4.2 3z" fill="var(--like)"/></svg>Like</p>
  </article>
  <article class="panel card" style="top:484px">
    <h2 class="card-head">Lady changed her status</h2>
    <div class="photo" role="img" aria-label="Member profile photo"></div>
    <p class="card-text">Lorem ipsum dolor sit amet, consectetur adipiscing elit. Maecenas fermentum ante id pellentesque consequat.</p>
    <p class="card-time">TuesDay 22:37</p>
    <p class="card-like"><svg width="9" height="8" viewBox="0 0 10 9"><path d="M5 9 0.8 4.6A2.4 2.4 0 0 1 5 1.6a2.4 2.4 0 0 1 4.2 3z" fill="var(--like)"/></svg>Like</p>
  </article>
  <article class="panel card" style="top:651px">
    <h2 class="card-head">Lady changed her status</h2>
    <div class="photo" role="img" aria-label="Member profile photo"></div>
    <p class="card-text">Lorem ipsum dolor sit amet, consectetur adipiscing elit. Maecenas fermentum ante id pellentesque consequat.</p>
    <p class="card-time">TuesDay 22:37</p>
    <p class="card-like"><svg width="9" height="8" viewBox="0 0 10 9"><path d="M5 9 0.8 4.6A2.4 2.4 0 0 1 5 1.6a2.4 2.4 0 0 1 4.2 3z" fill="var(--like)"/></svg>Like</p>
  </article>
  <article class="panel card" style="top:817px">
    <h2 class="card-head">Lady changed her status</h2>
    <div class="photo" role="img" aria-label="Member profile photo"></div>
    <p class="card-text">Lorem ipsum dolor sit amet, consectetur adipiscing elit. Maecenas fermentum ante id pellentesque consequat.</p>
    <p class="card-time">TuesDay 22:37</p>
    <p class="card-like"><svg width="9" height="8" viewBox="0 0 10 9"><path d="M5 9 0.8 4.6A2.4 2.4 0 0 1 5 1.6a2.4 2.4 0 0 1 4.2 3z" fill="var(--like)"/></svg>Like</p>
  </article>
</main>

<section class="panel matches">
  <span style="left:38px">Tavi</span>
  <span style="left:134px">Otis</span>
</section>

<section class="panel bg-select">
  <div class="pill pill--blue" style="top:10px">BACKGROUND SELECT</div>
  <div class="thumb" role="img" aria-label="Teal texture background" style="left:8px;top:48px;background:#2a6f78"></div>
  <div class="thumb" role="img" aria-label="Green bokeh background" style="left:74px;top:48px;background:linear-gradient(135deg,#b7dc6a,#6fb33a)"></div>
  <div class="thumb" role="img" aria-label="Night sky background" style="left:140px;top:48px;background:linear-gradient(135deg,#1a1850,#5a3d9a)"></div>
  <div class="thumb" role="img" aria-label="Sunburst background" style="left:8px;top:110px;background:linear-gradient(135deg,#f6d24a,#dff0f8)"></div>
  <div class="thumb" role="img" aria-label="Blue wave background" style="left:74px;top:110px;background:linear-gradient(135deg,#0a1f6b,#2f6fe0)"></div>
  <div class="thumb" role="img" aria-label="Clouds background" style="left:140px;top:110px;background:#3fb6ee"></div>
  <div class="thumb" role="img" aria-label="Bark texture background" style="left:8px;top:171px;background:linear-gradient(90deg,#8c8a84,#c4c0b6)"></div>
  <div class="thumb" role="img" aria-label="Teal rays background" style="left:74px;top:171px;background:linear-gradient(135deg,#1c7488,#3b93a4)"></div>
  <div class="thumb" role="img" aria-label="Pale pattern background" style="left:140px;top:171px;background:#dfe1a3"></div>
  <div class="thumb" role="img" aria-label="Green bubbles background" style="left:8px;top:232px;background:#1e9a2a"></div>
  <div class="thumb" role="img" aria-label="Wood planks background" style="left:74px;top:232px;background:linear-gradient(180deg,#8a6a4c,#b38e68)"></div>
  <div class="thumb" role="img" aria-label="Green swirl background" style="left:140px;top:232px;background:linear-gradient(135deg,#d5f0d0,#3fae55)"></div>
</section>

<footer class="footer">
  <h4 style="left:41px">WinkAtWheel.com</h4>
  <ul style="left:41px"><li>Homepage</li><li>Mobile Site</li><li>Friendbook</li><li>Chatterly</li></ul>
  <h4 style="left:226px">Legal</h4>
  <ul style="left:226px"><li>General Conditions</li><li>Terms &amp; Conditions</li><li>Privacy Statement</li><li>Cookies Information</li></ul>
  <h4 style="left:419px">Support</h4>
  <ul style="left:419px"><li>Contact Us</li><li>FAQ's &amp; Help</li><li>Safe Dating Advice</li><li>Pricing Details</li></ul>
  <p class="copyright">©2013 WinkAtWheel.com, All Rights Reserved</p>
  <div class="tweet">Unable to connect to Chatterly at this time.</div>
  <svg class="tweet-tail" width="16" height="14" viewBox="0 0 16 14"><path d="M0 0H16L12 14Z" fill="var(--bubble)"/></svg>
  <p class="social" style="left:796px"><i></i>Like us on Friendbook</p>
  <p class="social" style="left:930px"><i></i>Follow us on Chatterly</p>
</footer>

</body>
</html>
```